LAYOUT design - home page for a NZ winery - needs to be modern design

- This is for a layout design of the home page only. No coding required.

- The design should be based around the attached HPID (home page information design) I've attached both a Word.doc and a PDF - these are the same. The table boxes are just for approximate placement of information – you DON'T have to make it look exactly like this. Information for you is in orange text. Words to go on the design in black text. Most instructions are in the HPID. The only change to the HPID is you can use either the white or grey background logo in the header.

- The design needs to be smart and the colours soft/subtle – lots of space with mainly white and soft grey colours… with just accents/splashes of a soft blue (code: PMS 647) or gold. If you wish to tone down the colours in the photos supplied you could try a design doing this… please don’t all try this! Maybe you could try an TRK watermark from their logo somewhere on the design. Please be creative.

- Expected standard of design examples: (Please DO NOT copy these exactly – they are just examples)
http://www.hollowvale.co.nz/
http://www.brackwin.co.nz/
http://www.tussockfold.com/

Width of content will be 1100 pixels when implemented as a web page. Header height (without nav bar) 150-160 pixels.

The winning PSD file will have to be provided as follows…
1. Canvas size of 2000px x 2000px - 72ppi in Adobe Photoshop (CS5 compatible)
2. Width of content section is 1100px wide - centered in the canvas
3. Any button rollovers/hovers in the PSD as hidden layers.
4. All fonts used must be Google fonts (except for the header fonts).
5. You will need to supply the chosen home page plus one example page (example page as a style guide for how all other pages will look). Example page is only the header and navigational bar at the top, an empty sector in the middle with a column (180 px wide) which can be left or right aligned which means the main sector is 920 pixels wide, and then the footer at the bottom of the page.

Target Market(s)

New Zealand and world market for those who like wine. Upmarket clients.

Requirements
Must have
• clean fresh look with lots of white and soft grey colours.

```html
<!DOCTYPE html>
<html lang="en">
<head>
<meta charset="utf-8">
<title>Tarrow Ridge – Home</title>
<link rel="stylesheet" href="https://fonts.googleapis.com/css2?family=Great+Vibes&family=Libre+Baskerville:ital@0;1&family=Open+Sans:wght@400;600&display=swap">
<style>
:root{
  --page:#efefef;
  --white:#ffffff;
  --grey-line:#d9d9d9;
  --dark:#333;
  --copy:#7a7a7a;
  --blue:#1f5e99;
  --footer:#e6e6e6;
  --bar:#2a2627;
}
*{box-sizing:border-box;margin:0;padding:0}
html,body{width:674px;height:1200px;overflow:hidden;background:var(--page)}
body{position:relative;font-family:"Libre Baskerville",Georgia,serif;color:var(--dark)}
.abs{position:absolute}

/* header */
.site-header{left:0;top:0;width:674px;height:68px;background:#f4f4f4}
.brand{left:74px;top:20px;display:flex;align-items:center;gap:5px}
.brand-dot{width:7px;height:7px;border-radius:50%;background:var(--dark)}
.brand-name{font-family:"Libre Baskerville",serif;font-size:13px;line-height:14px;color:var(--dark)}
.brand-tag{left:74px;top:40px;font-family:"Open Sans",sans-serif;font-size:4px;color:#666;white-space:nowrap}
.header-info{right:74px;top:6px;text-align:right}
.tagline{font-family:"Great Vibes",cursive;font-size:13px;color:#555;line-height:16px}
.phone{font-family:"Open Sans",sans-serif;font-weight:600;font-size:11.5px;color:var(--blue);margin-top:3px}
.address{font-family:"Open Sans",sans-serif;font-size:6.4px;color:#666;margin-top:5px}

.main-nav{left:0;top:68px;width:674px;height:32px;background:linear-gradient(#f7f7f7,#e4e4e4);border-top:1px solid #e0e0e0}
.main-nav ul{list-style:none;display:flex;position:absolute;left:74px;top:0;height:32px;border-left:1px solid #ddd}
.main-nav li{font-family:"Open Sans",sans-serif;font-size:6.4px;color:#777;height:32px;line-height:32px;padding:0 8.5px;border-right:1px solid #ddd}
.main-nav li.active{color:var(--blue);background:#f9f9f9}

/* hero */
.hero{left:0;top:100px;width:674px;height:308px;background:linear-gradient(180deg,#b9b8b3 0%,#d6d0c2 30%,#d9cfb9 48%,#7f8a7a 56%,#6f7a66 63%,#c2aa80 70%,#9a7e2e 80%,#b08a22 90%,#6e5a18 100%)}
.hero-arrow{width:23px;height:23px;border-radius:50%;background:rgba(120,120,120,.55);top:142px}
.hero-arrow svg{position:absolute;left:7px;top:6px}

/* feature tiles */
.tile{width:162px;height:110px;border:1px solid #bbb;box-shadow:0 1px 3px rgba(0,0,0,.25)}
.tile::after{content:"";position:absolute;inset:5px;border:1px solid rgba(255,255,255,.7)}
.tile-label{position:absolute;left:0;right:0;top:49px;text-align:center;font-size:10.5px;color:#fff;text-shadow:0 1px 2px rgba(0,0,0,.6);z-index:1}
.tile-text{position:absolute;left:12px;right:8px;top:31px;text-align:center;font-style:italic;font-size:6.2px;line-height:12px;color:#fff;z-index:1}
.tile-btn{position:absolute;left:51px;top:75px;width:66px;height:18px;border:1px solid #fff;border-radius:9px;font-size:6px;color:#fff;text-align:center;line-height:16px;z-index:2}

/* content boxes */
.band{left:0;top:710px;width:674px;height:268px;background:#f2f2f2}
.card{background:var(--white);border:1px solid var(--grey-line)}
.card-title{position:absolute;left:6px;top:8px;font-size:9.5px;font-weight:400;color:var(--blue)}
.photo{position:absolute}
.body-copy{font-size:6.2px;line-height:11.6px;color:var(--copy)}
.small-copy{font-style:italic;font-size:5.2px;line-height:9.4px;color:var(--copy)}
.btn{position:absolute;background:var(--blue);color:#fff;font-size:6.4px;text-align:center;line-height:16px;border-radius:2px}
.blog-list{position:absolute;left:8px;right:10px;top:33px;list-style:none}
.blog-list li{position:relative;padding-left:14px;font-style:italic;font-size:5.8px;line-height:10px;color:#999;border-bottom:1px solid #e4e4e4;padding-bottom:6px;margin-bottom:8px}
.blog-list li:last-child{border:none}
.blog-list li b{font-weight:400;color:var(--blue)}
.blog-list svg{position:absolute;left:0;top:1px}

/* footer */
.site-footer{left:0;top:978px;width:674px;height:188px;background:var(--footer)}
.f-col{position:absolute;top:21px}
.f-head{font-size:8.8px;color:var(--dark);margin-bottom:11px}
.f-head.blue{color:var(--blue)}
.f-list{list-style:none;margin-top:-2px;margin-bottom:10px}
.f-list li{font-size:5.8px;color:var(--copy);line-height:13.6px;padding-left:10px;position:relative}
.f-list li::before{content:"";position:absolute;left:0;top:6px;width:5px;height:1.5px;background:var(--blue)}
.contact-list{list-style:none;font-style:italic;font-size:5.8px;line-height:12.3px;color:var(--copy)}
.contact-list li{padding-left:10px;position:relative}
.contact-list svg{position:absolute;left:0;top:3px}
.social{width:19px;height:19px;border-radius:50%;background:#c9c9c9;border:2px solid #eee}
.bottom-bar{left:0;top:1166px;width:674px;height:34px;background:var(--bar);font-family:"Open Sans",sans-serif;font-size:5.8px;color:#ccc}
</style>
</head>
<body>

<header class="site-header abs">
  <div class="brand abs">
    <span class="brand-dot"></span>
    <span class="brand-name">Tarrow Ridge</span>
  </div>
  <div class="brand-tag abs">WINE TOURS, RESTAURANT, CELLAR DOOR, WEDDINGS</div>
  <div class="header-info abs">
    <div class="tagline">New Zealand's best wine experience</div>
    <div class="phone">+64 6 555 0142</div>
    <div class="address">17 Stonebank Rd, Martinborough, New Zealand</div>
  </div>
</header>

<nav class="main-nav abs">
  <ul>
    <li class="active">Home</li><li>About Us</li><li>Buy Wine</li><li>Wine Tours</li><li>Accommodation</li><li>Restaurant</li><li>Weddings &amp; Events</li><li>Wine Club</li><li>Resource Centre</li><li>Contact</li>
  </ul>
</nav>

<section class="hero abs" role="img" aria-label="Hot air balloons drifting over autumn vineyards with hills behind">
  <div class="hero-arrow abs" style="left:18px"><svg width="9" height="11"><path d="M6 1 L2 5.5 L6 10" stroke="#fff" stroke-width="1.5" fill="none"/></svg></div>
  <div class="hero-arrow abs" style="left:635px"><svg width="9" height="11"><path d="M3 1 L7 5.5 L3 10" stroke="#fff" stroke-width="1.5" fill="none"/></svg></div>
</section>

<div class="tile abs" style="left:74px;top:434px;background:linear-gradient(135deg,#e2d6d0 0%,#c99a94 45%,#8e5c57 100%)" role="img" aria-label="Glass of rosé wine"><span class="tile-label">BUY WINE</span></div>
<div class="tile abs" style="left:256px;top:434px;background:linear-gradient(135deg,#5a4634 0%,#3a2c20 50%,#17110c 100%)" role="img" aria-label="Winemaker among barrels in the cellar"><span class="tile-label">WINE TOURS</span></div>
<div class="tile abs" style="left:438px;top:434px;background:linear-gradient(180deg,#c4ced0 0%,#a9b29c 50%,#5f6e3e 100%)" role="img" aria-label="Cottage among trees"><span class="tile-label">ACCOMMODATION</span></div>
<div class="tile abs" style="left:74px;top:565px;background:linear-gradient(180deg,#6f97c8 0%,#9a7a6a 50%,#4e3626 100%)" role="img" aria-label="Restaurant terrace with umbrellas"><span class="tile-label">RESTAURANT</span></div>
<div class="tile abs" style="left:256px;top:565px;background:linear-gradient(180deg,#cdc8be 0%,#b7a980 50%,#7d6a2c 100%)" role="img" aria-label="Balloons over the vineyard"><span class="tile-label">WEDDINGS &amp; EVENTS</span></div>
<div class="tile abs" style="left:438px;top:565px;background:linear-gradient(135deg,#6d5a4a,#3a2d24)" role="img" aria-label="Barrel room">
  <p class="tile-text">The Resource Centre has Tarrow Ridge Estate Accolades, Media bottle &amp; label photos, Tasting Notes, Image Library, Testimonials &amp; more…</p>
  <span class="tile-btn">READ MORE</span>
</div>

<section class="band abs"></section>

<article class="card abs" style="left:74px;top:726px;width:163px;height:234px">
  <h2 class="card-title">What's Happening at TRK...</h2>
  <div class="photo" style="left:6px;top:27px;width:151px;height:100px;background:linear-gradient(180deg,#b4c6d8 0%,#7f8f86 45%,#3f5a36 70%,#6c8a3e 100%);border:2px solid #ddd" role="img" aria-label="Three wine bottles in front of the vineyard"></div>
  <p class="body-copy abs" style="left:5px;top:140px;width:152px">Exciting times at Tarrow Ridge Estate... we've just revealed our new branding and the website has a fresh new look to reflect this. TRK is looking forward to an eventful and prosperous year so please come and visit us when you're next in the Martinborough region......</p>
</article>

<article class="card abs" style="left:255px;top:726px;width:164px;height:104px">
  <h2 class="card-title" style="left:10px">Social feed</h2>
</article>

<article class="card abs" style="left:255px;top:837px;width:164px;height:123px">
  <h2 class="card-title" style="left:10px;top:11px">Wine Blog</h2>
  <ul class="blog-list">
    <li><svg width="9" height="9"><circle cx="4.5" cy="4.5" r="4.5" fill="#1f5e99"/><path d="M3.5 2.5 L5.5 4.5 L3.5 6.5" stroke="#fff" fill="none"/></svg>Boutique vineyards excluded from <b>Kea Air in-flight</b> and airport lounge wine selections...</li>
    <li><svg width="9" height="9"><circle cx="4.5" cy="4.5" r="4.5" fill="#1f5e99"/><path d="M3.5 2.5 L5.5 4.5 L3.5 6.5" stroke="#fff" fill="none"/></svg>No need to take your wine on holiday now!...</li>
    <li><svg width="9" height="9"><circle cx="4.5" cy="4.5" r="4.5" fill="#1f5e99"/><path d="M3.5 2.5 L5.5 4.5 L3.5 6.5" stroke="#fff" fill="none"/></svg>Sheep versus Machines - Who Wins?...</li>
  </ul>
</article>

<article class="card abs" style="left:437px;top:726px;width:164px;height:104px">
  <h2 class="card-title" style="left:10px">Join us...</h2>
  <p class="small-copy abs" style="left:10px;top:27px;width:92px">Join the Tarrow Ridge Estate Wine Club today wine and receive a "buy one get one free" Grape to Glass Wine Tour Voucher.</p>
  <div class="photo" style="left:108px;top:27px;width:42px;height:36px;background:linear-gradient(180deg,#9fb2c4 0%,#7a5a4a 60%,#4a2a22 100%);border:2px solid #ddd" role="img" aria-label="Glass of red wine"></div>
  <span class="btn" style="left:107px;top:77px;width:45px;height:16px">JOIN NOW</span>
</article>

<article class="card abs" style="left:437px;top:837px;width:164px;height:123px">
  <h2 class="card-title" style="left:10px;top:11px">Gift Vouchers...</h2>
  <div class="photo" style="left:12px;top:29px;width:140px;height:53px;background:linear-gradient(135deg,#b8b0c8 0%,#5a6aa0 45%,#1e2a5a 100%)" role="img" aria-label="Hand holding dark grapes"></div>
  <p class="small-copy abs" style="left:12px;top:88px;width:105px">Give the gift of New Zealand's best wine experience! Vouchers include accommodation and wine tour options</p>
  <span class="btn" style="left:120px;top:96px;width:35px;height:16px">GIFT</span>
</article>

<footer class="site-footer abs">
  <div class="f-col" style="left:74px">
    <div class="f-head">Home</div>
    <div class="f-head" style="margin-top:19px">About Us</div>
    <ul class="f-list"><li>The Vineyard &amp; Terroir</li><li>Winemaking</li><li>The Team</li><li>Photos</li><li>塔罗</li></ul>
  </div>
  <div class="f-col" style="left:174px">
    <div class="f-head">Resource Centre</div>
    <ul class="f-list"><li>Tasting Notes</li><li>Image Library</li><li>Accolades</li><li>Videos</li><li>About Us Info</li><li>Testimonials</li></ul>
  </div>
  <div class="f-col" style="left:278px">
    <div class="f-head">Buy Wine</div>
    <ul class="f-list"><li>Our Wines</li><li>Distribution</li><li>Online Shop</li><li>Terms &amp; Conditions</li></ul>
    <div class="f-head">Wine Tours</div>
    <ul class="f-list"><li>Grape to Glass Tour</li><li>Casual tastings/ Cellar door</li></ul>
  </div>
  <div class="f-col" style="left:386px">
    <div class="f-head">Accommodation</div>
    <ul class="f-list"><li>The Winemakers Cottage</li><li>Packages / Special Offers</li></ul>
    <div class="f-head blue" style="margin-bottom:7px">Restaurant</div>
    <div class="f-head blue" style="margin-bottom:7px">Weddings &amp; Events</div>
    <div class="f-head blue">Wine Club</div>
  </div>
  <div class="f-col" style="left:494px">
    <div class="f-head">Contact</div>
    <ul class="contact-list">
      <li><svg width="6" height="6"><path d="M3 0 L6 3 L5 3 L5 6 L1 6 L1 3 L0 3Z" fill="#1f5e99"/></svg>Tarrow Ridge Estate</li>
      <li><svg width="6" height="6"><path d="M1 0 L2.5 0 L3 2 L2 2.8 Q3 4.5 4 4 L4.5 3.2 L6 4 L6 5.5 Q3 6.5 0.5 2.5Z" fill="#1f5e99"/></svg>Phone: +64 6 555 0142</li>
      <li><svg width="6" height="7"><path d="M3 7 L0.5 3 A2.5 2.5 0 1 1 5.5 3Z" fill="#1f5e99"/></svg>17 Stonebank Road</li>
      <li>Martinborough, New Zealand</li>
    </ul>
    <div class="abs" style="left:3px;top:97px;width:103px;height:40px;background:linear-gradient(135deg,#e8e4d6,#cfd6c4);border:2px solid #fff" role="img" aria-label="Location map"></div>
  </div>
  <div class="social abs" style="left:502px;top:165px"></div>
  <div class="social abs" style="left:528px;top:165px"></div>
  <div class="social abs" style="left:554px;top:165px"></div>
  <div class="social abs" style="left:580px;top:165px"></div>
</footer>

<div class="bottom-bar abs">
  <span class="abs" style="left:74px;top:12px">© Copy Rights 2014 Winery in Newzealand.All Rights Reserved</span>
  <span class="abs" style="left:630px;top:10px">C4</span>
</div>

</body>
</html>
```